Postcard Design

business name: COZY HOUR HELPER. I am a mother of 2 well adjusted, successful teenage boys. I decided to start this company caring for kids who are home sick, unable to go to daycare or school, and when their parent cant stay home with them. I was also a career woman for many years, with no friends available or family nearby to help when i was in an emergency situation for childcare. I know how stressful it can be when a child gets sick suddenly and unexpectedly. I would like to help out those parents in need, that have pressing schedules and a sick child at home that they really want to take care of, but cant due to their work pressures and priorities. I want parents to know that their child is safe and I can help them when in need, at last minute. The design should show the child is safe and well cared for and the parent is at ease, able to accomplish their obligations. I have also founded a nonprofit environmental education program in which I teach children in youth summer camps. I have taught creativity arts combined with science curriculum in kindergarten to 8th grade non-formal teaching for the past 5 years. This is a small community, and many people know me. I will be handing out these postcards to local daycares and people I know.

Industry/Entity Type

Business

```html
<!DOCTYPE html>
<html lang="en">
<head>
<meta charset="utf-8">
<title>Cozy Hour Helper – Postcards</title>
<link href="https://fonts.googleapis.com/css2?family=Roboto:ital,wght@0,400;0,500;0,700;1,400&display=swap" rel="stylesheet">
<style>
  :root {
    --page: #ececea;
    --orange: #e05a28;
    --teal: #17a2b0;
    --cream: #ede3b5;
    --panel: #f6f6f4;
    --white: #ffffff;
    --ink: #5a5a5a;
    --photo-warm-a: #e9d6b8;
    --photo-warm-b: #b78a5e;
    --photo-cool-a: #c9b08a;
    --photo-cool-b: #6d8fa8;
    --blocks-a: #d9554a;
    --blocks-b: #4f9ad3;
  }
  * { box-sizing: border-box; margin: 0; padding: 0; }
  html, body { width: 936px; height: 1200px; overflow: hidden; }
  body {
    background: var(--page);
    font-family: "Roboto", Arial, sans-serif;
    position: relative;
  }
  .postcard {
    position: absolute;
    left: 136px;
    width: 664px;
    height: 518px;
    background: var(--cream);
    overflow: hidden;
    box-shadow: 0 4px 14px rgba(0,0,0,.18);
  }
  .postcard--front { top: 62px; }
  .postcard--back { top: 630px; }
  .patchwork { position: absolute; inset: 0; }

  .title-box {
    position: absolute;
    background: var(--orange);
    border: 6px solid var(--white);
    color: var(--white);
    text-align: center;
    display: flex;
    flex-direction: column;
    justify-content: center;
    font-weight: 500;
    line-height: 1.05;
  }
  .title-box .title-main { font-size: 39px; letter-spacing: .5px; }
  .title-box .title-sub { font-size: 44px; }
  .postcard--front .title-box { left: 34px; top: 54px; width: 256px; height: 172px; transform: rotate(-1.5deg); }
  .postcard--back .title-box { left: 36px; top: 28px; width: 328px; height: 142px; transform: rotate(-1deg); }

  .photo {
    position: absolute;
  }
  .photo--front {
    left: 276px; top: 38px; width: 382px; height: 262px;
    border: 8px solid var(--white);
    transform: rotate(3deg);
    background: linear-gradient(135deg, var(--photo-warm-a), var(--photo-warm-b) 60%, #d3dbe8);
    box-shadow: 0 3px 8px rgba(0,0,0,.2);
  }
  .photo--back {
    left: 394px; top: 126px; width: 270px; height: 392px;
    background: linear-gradient(160deg, #b89468, var(--photo-cool-a) 45%, var(--photo-cool-b));
  }

  .info-panel {
    position: absolute;
    background: var(--white);
  }
  .postcard--front .info-panel { left: 14px; top: 226px; width: 350px; height: 292px; padding: 20px 16px 0 16px; }
  .postcard--back .info-panel { left: 15px; top: 160px; width: 380px; height: 264px; background: var(--panel); padding: 30px 22px 0; text-align: center; }

  .lead { color: var(--teal); font-size: 20px; font-weight: 400; margin-bottom: 10px; }
  .needs { list-style: none; color: var(--ink); font-size: 17px; line-height: 1.6; }
  .needs li { display: flex; gap: 8px; align-items: flex-start; }
  .needs svg { flex: none; margin-top: 6px; }

  .blocks {
    position: absolute; left: 4px; top: 170px; width: 104px; height: 92px;
    background: linear-gradient(135deg, var(--blocks-a), #f2c84b 50%, var(--blocks-b));
    border-radius: 4px;
    transform: rotate(-8deg);
  }
  .reassure {
    position: absolute; left: 126px; top: 180px; width: 214px;
    color: var(--ink); font-size: 15px; font-style: italic; text-align: center; line-height: 1.25;
  }

  .promise {
    position: absolute; left: 404px; top: 334px; width: 246px;
    color: var(--orange); font-size: 20px; font-weight: 500; text-align: center; line-height: 1.35;
  }

  .contact {
    position: absolute; background: var(--orange); color: var(--white);
    text-align: center; display: flex; flex-direction: column; justify-content: center; gap: 4px;
  }
  .postcard--front .contact { left: 381px; top: 412px; width: 283px; height: 106px; border-left: 7px solid var(--white); border-top: 7px solid var(--white); }
  .postcard--back .contact { left: 0; top: 422px; width: 396px; height: 96px; }
  .contact-name { font-size: 20px; font-weight: 500; }
  .contact-phone { font-size: 22px; font-weight: 500; display: flex; align-items: center; justify-content: center; gap: 8px; }

  .headline-teal { color: var(--teal); font-size: 20px; font-weight: 700; margin-bottom: 24px; }
  .story { color: var(--ink); font-size: 15px; font-style: italic; line-height: 1.3; margin-bottom: 30px; }
  .experience { color: var(--orange); font-size: 17px; font-weight: 700; }
</style>
</head>
<body>

<section class="postcard postcard--front">
  <svg class="patchwork" width="664" height="518" viewBox="0 0 664 518" aria-hidden="true">
    <rect width="664" height="518" fill="#ede3b5"/>
    <g stroke="#fbf3d8" stroke-width="4">
      <rect x="0" y="0" width="150" height="72" fill="#cddcb8"/>
      <rect x="150" y="0" width="72" height="60" fill="#b7d2cc"/>
      <rect x="222" y="0" width="130" height="52" fill="#f4b97d"/>
      <rect x="352" y="0" width="170" height="46" fill="#cddcb8"/>
      <rect x="522" y="0" width="36" height="62" fill="#b7d2cc"/>
      <rect x="558" y="0" width="106" height="64" fill="#f1cdbb"/>
      <rect x="0" y="72" width="60" height="72" fill="#f7dcaa"/>
      <rect x="0" y="144" width="40" height="84" fill="#cddcb8"/>
      <rect x="600" y="300" width="64" height="60" fill="#f5dfb0"/>
    </g>
  </svg>

  <div class="title-box">
    <span class="title-main">COZY HOUR</span>
    <span class="title-sub">helper</span>
  </div>

  <div class="photo photo--front" role="img" aria-label="Photo of a young boy in bed playing doctor with a stethoscope on a teddy bear"></div>

  <div class="info-panel">
    <p class="lead">Caring for kids who...</p>
    <ul class="needs">
      <li><svg width="11" height="11" viewBox="0 0 11 11"><circle cx="5.5" cy="5.5" r="5.5" fill="#17a2b0"/><path d="M4.3 3.2 L6.6 5.5 L4.3 7.8" stroke="#fff" stroke-width="1.5" fill="none"/></svg>are home sick</li>
      <li><svg width="11" height="11" viewBox="0 0 11 11"><circle cx="5.5" cy="5.5" r="5.5" fill="#17a2b0"/><path d="M4.3 3.2 L6.6 5.5 L4.3 7.8" stroke="#fff" stroke-width="1.5" fill="none"/></svg>unable to go to daycare or school</li>
      <li><svg width="11" height="11" viewBox="0 0 11 11"><circle cx="5.5" cy="5.5" r="5.5" fill="#17a2b0"/><path d="M4.3 3.2 L6.6 5.5 L4.3 7.8" stroke="#fff" stroke-width="1.5" fill="none"/></svg>when their parent cant stay home with them.</li>
    </ul>
    <div class="blocks" role="img" aria-label="Illustration of colourful alphabet blocks spelling child care"></div>
    <p class="reassure">I know how stressful it can be when a child gets sick suddenly and unexpectedly.</p>
  </div>

  <p class="promise">I can help you<br>at last minute!</p>

  <div class="contact">
    <span class="contact-name">Mara Lindqvist</span>
    <span class="contact-phone">
      <svg width="20" height="20" viewBox="0 0 20 20" aria-hidden="true"><circle cx="10" cy="10" r="8.5" fill="none" stroke="#fff" stroke-width="1.8"/><path d="M7 5.5 L8.6 5.3 L9.3 7.8 L8.3 8.6 Q9.3 10.8 11.4 11.8 L12.2 10.8 L14.6 11.5 L14.4 13.1 Q11.8 14.4 8.9 11.6 Q6 8.6 7 5.5 Z" fill="#fff"/></svg>
      (555) 201-4476
    </span>
  </div>
</section>

<section class="postcard postcard--back">
  <svg class="patchwork" width="664" height="518" viewBox="0 0 664 518" aria-hidden="true">
    <rect width="664" height="518" fill="#ede3b5"/>
    <g stroke="#fbf3d8" stroke-width="4">
      <rect x="0" y="0" width="40" height="86" fill="#cddcb8"/>
      <rect x="0" y="86" width="40" height="90" fill="#f7dcaa"/>
      <rect x="180" y="0" width="70" height="30" fill="#b7d2cc"/>
      <rect x="250" y="0" width="160" height="26" fill="#f4b97d"/>
      <rect x="364" y="26" width="60" height="100" fill="#f7dcaa"/>
      <rect x="424" y="0" width="160" height="50" fill="#cddcb8"/>
      <rect x="584" y="0" width="34" height="36" fill="#b7d2cc"/>
      <rect x="618" y="0" width="46" height="36" fill="#f1cdbb"/>
      <rect x="424" y="50" width="160" height="76" fill="#dfe2b0"/>
      <rect x="584" y="36" width="80" height="40" fill="#cddcb8"/>
      <rect x="584" y="76" width="80" height="50" fill="#f5d6a8"/>
    </g>
  </svg>

  <div class="title-box">
    <span class="title-main">COZY HOUR</span>
    <span class="title-sub">helper</span>
  </div>

  <div class="info-panel">
    <p class="headline-teal">I can help you at last minute!</p>
    <p class="story">I would like to help out those parents in need, that have pressing schedules and a sick child at home that they really want to take care of, but cant due to their work pressures and priorities.</p>
    <p class="experience">14 years of childcare experience!</p>
  </div>

  <div class="photo photo--back" role="img" aria-label="Photo of a smiling young girl hugging a teddy bear"></div>

  <div class="contact">
    <span class="contact-name">Mara Lindqvist</span>
    <span class="contact-phone">
      <svg width="20" height="20" viewBox="0 0 20 20" aria-hidden="true"><circle cx="10" cy="10" r="8.5" fill="none" stroke="#fff" stroke-width="1.8"/><path d="M7 5.5 L8.6 5.3 L9.3 7.8 L8.3 8.6 Q9.3 10.8 11.4 11.8 L12.2 10.8 L14.6 11.5 L14.4 13.1 Q11.8 14.4 8.9 11.6 Q6 8.6 7 5.5 Z" fill="#fff"/></svg>
      (555) 201-4476
    </span>
  </div>
</section>

</body>
</html>
```